Business Card Design Project: Classically Trained Singer and Voice Teacher

I am a classically trained singer that performs in Opera and Musical Theater and also teaches private voice lessons in those fields. I am looking for a business card that I can give to casting directors and colleagues, as well as to people who are interested in taking voice lessons from me.

This is sort of like an actors business card so I want my headshot and name to be the main focus.

I was kind of thinking of having the business card be horizontal with my headshot photo on the front taking up roughly half and my information on the same side, and perhaps my name again on the back or some form of my initials. But I am totally open to other options for layout.I would prefer to have a double sided business card, but once again, its not essential.

I am looking for it to look and feel elegant artistic and professional, without looking feminine.

Because of the colors of my headshot I would imagine that it would be predominantly brown and white, but I am totally open to other approaches.feel totally free to crop my headshot so that it fits better into your overall design and layout.

It is highly likely that I will ask the winner of the design to create a flyer for marketing my voice lessons with a similar look.

If you have any questions or clarifications, please feel free to ask.

Target Market(s)

Opera and Musical theater casting directors, colleagues; potential voice lesson students

Industry/Entity Type

Marketing

Requirements
Must have
• These must feature prominently:
- (My Headshot (attached))
- Marlow Kitteridge (my name)

These dont need to be as prominent:
- Baritone
- Private Voice Teacher
- Opera and Musical Theater

Contact Info:
Phone: (555) 384-7261
Email: marlokitt@quellmail.example

Nice to have
• Double sided

```html
<!DOCTYPE html>
<html lang="en">
<head>
<meta charset="utf-8">
<title>Marlow Kitteridge — Business Card</title>
<link rel="stylesheet" href="https://fonts.googleapis.com/css2?family=Bebas+Neue&display=swap">
<style>
  :root {
    --page: #ffffff;
    --card-brown: #53443c;
    --ribbon-cream: #f5f1e6;
    --ink-white: #ffffff;
    --accent-teal: #1e9b94;
    --accent-orange: #e0561f;
    --photo-light: #8a8f96;
    --photo-mid: #6b5040;
    --photo-dark: #3b2a22;
  }
  * { box-sizing: border-box; margin: 0; padding: 0; }
  html, body {
    width: 1200px;
    height: 900px;
    overflow: hidden;
    background: var(--page);
  }
  body {
    position: relative;
    font-family: "Bebas Neue", "Arial Narrow", sans-serif;
  }
  .card {
    position: absolute;
    left: 264px;
    width: 672px;
    height: 384px;
    background: var(--card-brown);
    overflow: hidden;
  }
  .card--front { top: 50px; }
  .card--back { top: 458px; }

  .headshot {
    position: absolute;
    left: 0;
    top: 0;
    width: 276px;
    height: 384px;
    background:
      linear-gradient(100deg, var(--photo-light) 0%, #a9adb2 18%, transparent 40%),
      radial-gradient(ellipse 55% 40% at 55% 30%, #c79a82 0%, transparent 70%),
      linear-gradient(180deg, #9c8e84 0%, var(--photo-mid) 55%, var(--photo-dark) 100%);
  }

  .name-ribbon {
    position: absolute;
    left: 266px;
    top: 156px;
    width: 382px;
    height: 64px;
  }
  .name-ribbon svg {
    position: absolute;
    inset: 0;
  }
  .name-ribbon .name {
    position: absolute;
    left: 38px;
    top: 0;
    line-height: 64px;
    font-size: 38px;
    letter-spacing: 3px;
    color: var(--card-brown);
    white-space: nowrap;
  }

  .contact {
    position: absolute;
    left: 302px;
    top: 280px;
    color: var(--ink-white);
    list-style: none;
  }
  .contact li {
    white-space: nowrap;
    line-height: 34px;
  }
  .contact .phone { font-size: 26px; letter-spacing: 5px; }
  .contact .email { font-size: 23px; letter-spacing: 2px; }

  .roles {
    position: absolute;
    left: 100px;
    top: 248px;
    list-style: none;
  }
  .roles li {
    font-size: 25px;
    letter-spacing: 3px;
    line-height: 34px;
    white-space: nowrap;
  }
  .roles .voice-type { color: var(--accent-teal); }
  .roles .teaching { color: var(--accent-orange); }
  .roles .genres { color: var(--ink-white); }
</style>
</head>
<body>
  <section class="card card--front" aria-label="Card front">
    <div class="headshot" role="img" aria-label="Headshot of Marlow Kitteridge"></div>

    <div class="name-ribbon">
      <svg width="382" height="64" viewBox="0 0 382 64" aria-hidden="true">
        <polygon points="0,0 382,0 358,32 382,64 0,64" fill="var(--ribbon-cream)"/>
      </svg>
      <h1 class="name">Marlow Kitteridge</h1>
    </div>

    <ul class="contact">
      <li class="phone">T : 555.384.7261</li>
      <li class="email">marlokitt@quellmail.example</li>
    </ul>
  </section>

  <section class="card card--back" aria-label="Card back">
    <ul class="roles">
      <li class="voice-type">Baritone</li>
      <li class="teaching">Private Voice Teacher</li>
      <li class="genres">Opera and Musical Theatre</li>
    </ul>
  </section>
</body>
</html>
```